Spring Detox sale graphics for social media

You MUST read the Brief in the WORD document and follow the instructions there. I want to create 10 social media graphics (new Instagram size 4:5 (1080 x 1350 pixels) focusing on our Mother’s Day Spring Detox Sale graphics, using any of the pics attached. Use the attached pics, NO RANDOM STOCK PHOTOGRAPHY. For the color scheme of the graphics, they should all be complementary to the product colors or feel like Spring time.

Target Market(s)

primarily women

Requirements
Must have
• the photos and text attached

```html
<!DOCTYPE html>
<html lang="en">
<head>
<meta charset="utf-8">
<title>Mother's Day Spring Detox Sale – Social Set</title>
<link rel="stylesheet" href="https://fonts.googleapis.com/css2?family=Bebas+Neue&family=Oswald:wght@300;400;700&display=swap">
<style>
:root{
  --canvas:#232323;
  --white:#ffffff;
  --ink:#1f1f1f;
  --green:#2f5247;
  --red:#ef3434;
  --navy:#2b3a8f;
  --purple:#7b4a85;
  --plum:#5a2a4c;
  --blue:#3a8ef0;
  --photo-a:#d9cfc8;
  --photo-b:#6b4a3c;
  --bottle-a:#f4f4f4;
  --bottle-b:#cfd3da;
}
*{margin:0;padding:0;box-sizing:border-box}
html,body{width:1200px;height:2774px;overflow:hidden;background:var(--canvas)}
.set{position:relative;width:1200px;height:2774px}
.post{position:absolute;width:386px;height:482px;overflow:hidden;background:var(--white)}
.col-l{left:204px}.col-r{left:611px}
.row-1{top:148px}.row-2{top:646px}.row-3{top:1144px}.row-4{top:1644px}.row-5{top:2144px}
.abs{position:absolute}
.bebas{font-family:"Bebas Neue","Oswald",sans-serif;line-height:1;white-space:nowrap}
.light{font-family:"Oswald",sans-serif;font-weight:300;line-height:1;white-space:nowrap}
.bold{font-family:"Oswald",sans-serif;font-weight:700;line-height:1;white-space:nowrap}
.center{text-align:center}
.bottles{background:linear-gradient(180deg,var(--bottle-a) 0%,var(--bottle-b) 100%);border-radius:14px;opacity:.95}
.photo{background:linear-gradient(160deg,var(--photo-a) 0%,#b89c8a 45%,var(--photo-b) 100%)}
.sketch{background:radial-gradient(circle at 50% 45%,#f3f0f0 0%,#e4dede 70%,rgba(255,255,255,0) 72%)}
.band{display:flex;align-items:center;justify-content:center;color:var(--white)}
.shadow-bar{box-shadow:0 8px 8px -6px rgba(0,0,0,.55)}
</style>
</head>
<body>
<main class="set">

  <!-- 1 -->
  <section class="post col-l row-1">
    <svg class="abs" style="left:0;top:0" width="386" height="200"><polygon points="0,0 386,0 386,80 0,180" fill="var(--green)"/></svg>
    <div class="abs bottles" role="img" aria-label="Four supplement bottles in a row" style="left:30px;top:22px;width:326px;height:180px"></div>
    <div class="abs sketch" role="img" aria-label="Line drawing of mother holding baby" style="left:18px;top:205px;width:66px;height:66px"></div>
    <div class="abs bebas" style="left:96px;top:222px;font-size:56px;color:var(--green)">MOTHER’S DAY</div>
    <div class="abs band bebas shadow-bar" style="left:33px;top:280px;width:320px;height:56px;background:var(--red);font-size:46px">SPRING DETOX SALE</div>
    <div class="abs bebas center" style="left:0;top:348px;width:386px;font-size:76px;color:var(--navy)">25% OFF</div>
    <div class="abs band bold shadow-bar" style="left:68px;top:425px;width:250px;height:32px;background:var(--green);font-size:20px;font-weight:400;letter-spacing:5px">EVERYTHING!</div>
  </section>

  <!-- 2 -->
  <section class="post col-r row-1">
    <div class="abs photo" role="img" aria-label="Smiling woman in white top standing behind supplement bottles in a kitchen" style="left:0;top:0;width:386px;height:412px"></div>
    <div class="abs" role="img" aria-label="Soft pink silhouette of mother and child" style="left:0;top:0;width:200px;height:200px;background:linear-gradient(135deg,#ffffff 0%,#f6dfe6 50%,rgba(255,255,255,0) 100%)"></div>
    <div class="abs" style="left:12px;top:190px;width:202px;height:230px;background:var(--white);border-radius:14px 14px 0 0"></div>
    <div class="abs bebas" style="left:24px;top:230px;font-size:130px;color:var(--plum)">25</div>
    <div class="abs bebas" style="left:140px;top:238px;font-size:66px;color:var(--plum)">%</div>
    <div class="abs bebas" style="left:140px;top:296px;font-size:42px;color:var(--plum)">OFF</div>
    <div class="abs light" style="left:26px;top:352px;font-size:36px;color:var(--ink)">Mother’s Day</div>
    <div class="abs band bebas" style="left:0;top:412px;width:386px;height:70px;background:var(--red);font-size:52px">SPRING DETOX SALE</div>
  </section>

  <!-- 3 -->
  <section class="post col-l row-2" style="background:var(--purple)">
    <div class="abs photo" role="img" aria-label="Smiling woman in white top with supplement bottles on a counter" style="left:140px;top:0;width:246px;height:482px"></div>
    <div class="abs" style="left:17px;top:42px;width:220px;height:400px;background:var(--white);border-radius:16px"></div>
    <div class="abs bebas" style="left:40px;top:62px;font-size:130px;color:var(--blue)">25</div>
    <div class="abs bebas" style="left:156px;top:70px;font-size:66px;color:var(--blue)">%</div>
    <div class="abs bebas" style="left:156px;top:128px;font-size:44px;color:var(--blue)">OFF</div>
    <div class="abs bebas" style="left:38px;top:176px;font-size:30px;color:var(--ink)">ALL SUPPLEMENTS</div>
    <div class="abs bebas shadow-bar" style="left:38px;top:222px;width:140px;height:108px;background:var(--blue);color:var(--white);font-size:50px;padding:6px 0 0 12px;line-height:.95">SPRING<br>DETOX</div>
    <div class="abs bebas" style="left:40px;top:342px;font-size:90px;color:var(--red)">SALE!</div>
  </section>

  <!-- 4 -->
  <section class="post col-r row-2">
    <svg class="abs" style="left:0;top:0" width="386" height="220"><polygon points="0,0 386,0 386,200 0,80" fill="var(--navy)"/></svg>
    <div class="abs bottles" role="img" aria-label="Four supplement bottles in a row" style="left:30px;top:70px;width:326px;height:138px"></div>
    <div class="abs band bebas" style="left:33px;top:235px;width:320px;height:90px;background:var(--red);font-size:84px">25% OFF</div>
    <div class="abs bebas center" style="left:0;top:335px;width:386px;font-size:54px;color:var(--ink)">SPRING DETOX SALE</div>
    <div class="abs band bebas shadow-bar" style="left:46px;top:400px;width:294px;height:45px;background:var(--navy);font-size:25px">SPRING RESET. SUMMER READY</div>
  </section>

  <!-- 5 -->
  <section class="post col-l row-3">
    <svg class="abs" style="left:0;top:0" width="386" height="482"><polygon points="386,0 386,200 250,130" fill="var(--purple)"/></svg>
    <div class="abs photo" role="img" aria-label="Smiling woman in white top with supplement bottles in a kitchen" style="left:0;top:0;width:386px;height:482px;clip-path:polygon(386px 0,386px 482px,0 482px,0 360px)"></div>
    <div class="abs bebas" style="left:20px;top:14px;font-size:130px;color:var(--plum)">25</div>
    <div class="abs bebas" style="left:136px;top:22px;font-size:66px;color:var(--plum)">%</div>
    <div class="abs bebas" style="left:136px;top:80px;font-size:44px;color:var(--plum)">OFF</div>
    <div class="abs bebas" style="left:210px;top:130px;font-size:32px;color:var(--ink);transform:rotate(-90deg);transform-origin:left top">Everything</div>
    <div class="abs light" style="left:20px;top:132px;font-size:36px;color:var(--ink)">Mother’s Day</div>
    <div class="abs bebas" style="left:20px;top:176px;font-size:48px;line-height:.95;color:var(--purple)">SPRING<br>DETOX</div>
    <div class="abs bebas" style="left:20px;top:268px;font-size:48px;color:var(--ink)">SALE</div>
  </section>

  <!-- 6 -->
  <section class="post col-r row-3" style="background:var(--green)">
    <div class="abs" role="img" aria-label="Faint supplement bottle in background" style="left:200px;top:150px;width:186px;height:240px;background:linear-gradient(180deg,rgba(255,255,255,.08),rgba(255,255,255,.16));border-radius:20px"></div>
    <div class="abs" style="left:21px;top:26px;width:344px;height:430px;border:1.5px solid rgba(255,255,255,.7);border-radius:14px"></div>
    <div class="abs bebas" style="left:58px;top:40px;font-size:200px;color:var(--white)">25</div>
    <div class="abs bebas" style="left:248px;top:52px;font-size:110px;color:var(--white)">%</div>
    <div class="abs bebas" style="left:248px;top:140px;font-size:72px;color:var(--blue)">OFF</div>
    <div class="abs bebas center" style="left:0;top:222px;width:386px;font-size:60px;color:var(--white)">MOTHER’S DAY</div>
    <div class="abs" style="left:54px;top:278px;width:160px;height:2px;background:var(--blue)"></div>
    <div class="abs bebas center" style="left:0;top:282px;width:386px;font-size:60px;color:var(--white)">SALE</div>
    <div class="abs band bebas shadow-bar" style="left:55px;top:345px;width:276px;height:62px;background:var(--blue);font-size:34px">FEEL AMAZING AGAIN!</div>
  </section>

  <!-- 7 -->
  <section class="post col-l row-4">
    <div class="abs" style="left:0;top:0;width:386px;height:108px;background:var(--navy)"></div>
    <div class="abs bottles" role="img" aria-label="Four supplement bottles in a row" style="left:30px;top:25px;width:326px;height:140px"></div>
    <div class="abs sketch" role="img" aria-label="Line drawing of mother holding baby" style="left:28px;top:172px;width:112px;height:130px"></div>
    <div class="abs bebas" style="left:148px;top:178px;font-size:170px;color:var(--navy)">25</div>
    <div class="abs bebas" style="left:292px;top:184px;font-size:86px;color:var(--navy)">%</div>
    <div class="abs bebas" style="left:292px;top:258px;font-size:52px;color:var(--navy)">OFF</div>
    <div class="abs band bebas" style="left:28px;top:310px;width:358px;height:74px;background:var(--red);font-size:52px">MOTHER’S DAY SALE</div>
    <div class="abs bold center" style="left:28px;top:396px;width:358px;font-size:44px;color:var(--ink)">Refresh Your Body</div>
  </section>

  <!-- 8 -->
  <section class="post col-r row-4">
    <svg class="abs" style="left:0;top:0" width="386" height="482"><polygon points="0,340 386,270 386,482 0,482" fill="var(--purple)"/></svg>
    <div class="abs band bebas" style="left:30px;top:25px;width:328px;height:90px;background:var(--red);font-size:86px">25% OFF</div>
    <div class="abs bebas center" style="left:0;top:122px;width:386px;font-size:54px;color:var(--ink)">SPRING DETOX SALE</div>
    <div class="abs band bebas shadow-bar" style="left:27px;top:180px;width:331px;height:50px;background:var(--purple);font-size:28px">SPRING CLEANSE. SUMMER GLOW</div>
    <div class="abs bottles" role="img" aria-label="Four supplement bottles in a row" style="left:34px;top:262px;width:322px;height:178px"></div>
  </section>

  <!-- 9 -->
  <section class="post col-l row-5" style="background:var(--green)">
    <div class="abs bebas" style="left:26px;top:44px;font-size:92px;color:var(--white)">25%</div>
    <div class="abs bebas" style="left:24px;top:114px;font-size:112px;color:var(--white)">OFF</div>
    <div class="abs" style="left:170px;top:16px;width:186px;height:250px;background:var(--white);border-radius:16px"></div>
    <div class="abs bebas center" style="left:170px;top:34px;width:186px;font-size:54px;color:var(--navy)">MOTHER’S</div>
    <div class="abs bebas center" style="left:170px;top:82px;width:186px;font-size:64px;color:var(--navy)">DAY</div>
    <div class="abs bebas center" style="left:170px;top:136px;width:186px;font-size:96px;color:var(--navy)">SALE</div>
    <div class="abs bottles" role="img" aria-label="Four supplement bottles in a row" style="left:30px;top:218px;width:326px;height:212px"></div>
    <div class="abs band bebas" style="left:0;top:448px;width:386px;height:34px;background:var(--red);font-size:24px">DETOX THIS SPRING. SHINE THIS SUMMER</div>
  </section>

  <!-- 10 -->
  <section class="post col-r row-5">
    <div class="abs band bebas" style="left:0;top:0;width:255px;height:64px;background:var(--red);border-radius:0 32px 32px 0;font-size:54px">25% OFF</div>
    <div class="abs bebas" style="left:20px;top:72px;font-size:50px;color:var(--ink)">MOTHER’S DAY</div>
    <div class="abs bebas" style="left:18px;top:116px;font-size:52px;color:var(--red)">SALE</div>
    <div class="abs sketch" role="img" aria-label="Line drawing of mother holding baby" style="left:278px;top:4px;width:104px;height:160px"></div>
    <div class="abs bottles" role="img" aria-label="Four supplement bottles in a row" style="left:24px;top:178px;width:338px;height:150px"></div>
    <svg class="abs" style="left:0;top:300px" width="386" height="60"><ellipse cx="193" cy="18" rx="200" ry="26" fill="#1f1f1f"/></svg>
    <div class="abs bebas center" style="left:0;top:358px;width:386px;font-size:58px;color:var(--red)">SPRING DETOX FOR</div>
    <div class="abs bebas center" style="left:0;top:416px;width:386px;font-size:58px;color:var(--ink)">A SUMMER BODY</div>
  </section>

</main>
</body>
</html>
```